FinTech company looking to revamp and expand client-facing interface for our financial models

Pellworth Engines currently has a very simple website that allows clients to interact with our financial models. We are looking to completely redesign the current site and add several extra pages to provide extra functionality. We want the design to have a modern, slick feel, that will work on both a desktop or a tablet. It should be straightforward for clients to move between different pages at any time, and clear from the layout how to interact with the more advanced features. We have included screenshots of existing pages in the attached design brief, as well as sketches of the functionality required by the new pages, but can't provide a direct link to the current site.
Target Market(s)
Professional investors that will be paying to access the interface
Industry/Entity Type
Finance
Number of Pages Required
4 page
Colors
Designer to choose colors to be used in the design.
Look and feel
Each slider illustrates characteristics of the customer's brand and the style your logo design should communicate.

```html
<!DOCTYPE html>
<html lang="en">
<head>
<meta charset="utf-8">
<title>Pellworth Engines — ETF Pairs Models</title>
<link rel="stylesheet" href="https://fonts.googleapis.com/css2?family=Montserrat:wght@500;600;700&family=Roboto+Condensed:wght@400;500&display=swap">
<style>
:root{
  --page:#e8e8e8;
  --white:#ffffff;
  --navy:#0b3a6e;
  --ink:#1b1b1b;
  --teal:#006b64;
  --row-alt:#efefef;
  --rule:#e2e2e2;
  --tab:#ffffff;
  --muted:#555555;
}
*{box-sizing:border-box;margin:0;padding:0}
html,body{width:1200px;height:706px;overflow:hidden;background:var(--page)}
body{position:relative;font-family:"Montserrat",sans-serif;color:var(--ink)}
.app{position:absolute;left:14px;top:0;width:1172px;height:692px;background:linear-gradient(#f0f0f0,#ffffff 60%);}
.topbar{position:absolute;left:0;top:0;width:1172px;height:69px;background:var(--white);box-shadow:0 6px 10px rgba(0,0,0,.08);display:flex}
.brand{position:absolute;left:53px;top:0;line-height:69px;font-weight:700;font-size:17px}
.navitem{position:absolute;top:0;height:69px;display:flex;align-items:center;justify-content:center;gap:9px;font-weight:700;font-size:12.5px;border-right:1px solid var(--rule)}
.navitem.active{background:var(--navy);color:var(--white);border-right:none}
.navitem svg{width:22px;height:22px}
.tabs{position:absolute;left:0;top:0}
.tab{position:absolute;height:42px;background:var(--tab);border-radius:6px 6px 0 0;font-weight:600;font-size:12.5px;color:#333;display:flex;align-items:center;justify-content:center;padding-bottom:2px;box-shadow:0 -1px 4px rgba(0,0,0,.05)}
.tab.low{top:125px;height:32px;padding-top:6px}
.tab.mid{top:115px;height:42px}
.tab.current{top:106px;height:51px;background:var(--ink);color:var(--white);font-weight:700}
.tab.arrow{width:37px;left:1098px;top:125px;height:32px}
.tab.add{left:1140px;top:125px;width:37px;height:32px;background:var(--navy);border-radius:4px 4px 0 0}
.content{position:absolute;left:0;top:157px;width:1172px;height:535px;background:linear-gradient(#e3e3e3,#fafafa 80%)}
.export{position:absolute;left:1075px;top:197px;display:flex;align-items:center;gap:7px;color:var(--navy);font-weight:700;font-size:16.5px}
.filters{position:absolute;left:14px;top:309px;width:46px;height:231px;background:var(--ink);border-radius:0 6px 6px 0}
.filters span{position:absolute;left:50%;top:50%;transform:translate(-50%,-50%) rotate(-90deg);color:var(--white);font-weight:700;font-size:15px;letter-spacing:1.5px}
.filters svg{position:absolute;left:35px;top:104px}
.grid{position:absolute;left:97px;top:231px;width:1071px;border-collapse:collapse;table-layout:fixed;border-radius:8px;overflow:hidden;box-shadow:0 2px 8px rgba(0,0,0,.15);background:var(--white)}
.grid th{height:65px;color:var(--white);font-weight:600;font-size:16px;background:var(--teal);border-right:1px solid rgba(255,255,255,.15)}
.grid th.key{background:var(--ink);border-right:1px solid #3a3a3a}
.grid td{height:64px;font-family:"Roboto Condensed",sans-serif;font-size:15.5px;padding-left:9px;line-height:1.25;border-right:1px solid var(--rule)}
.grid td.id{text-align:center;padding-left:0}
.grid td.sector{padding-left:22px}
.grid tbody tr:nth-child(even) td{background:var(--row-alt)}
.grid td:last-child,.grid th:last-child{border-right:none}
</style>
</head>
<body>
<div class="app">
  <header class="topbar">
    <div class="brand">PLEXO</div>
    <div class="navitem active" style="left:166px;width:83px">250D</div>
    <div class="navitem" style="left:249px;width:83px">83D</div>
    <div class="navitem" style="left:332px;width:83px">42D</div>
    <div class="navitem" style="left:415px;width:125px"></div>
    <div class="navitem active" style="left:540px;width:131px">
      <svg viewBox="0 0 24 24" fill="none" stroke="#fff" stroke-width="2"><path d="M3 11 12 3l9 8"/><path d="M5 10v10h5v-6h4v6h5V10"/></svg>MODELS</div>
    <div class="navitem" style="left:671px;width:162px">
      <svg viewBox="0 0 24 24" fill="none" stroke="#222" stroke-width="1.6"><circle cx="12" cy="12" r="3"/><circle cx="12" cy="12" r="7" stroke-dasharray="2 2"/><circle cx="12" cy="3" r="1.5"/><circle cx="12" cy="21" r="1.5"/><circle cx="3" cy="12" r="1.5"/><circle cx="21" cy="12" r="1.5"/></svg>SENSITIVITIES</div>
    <div class="navitem" style="left:833px;width:148px">
      <svg viewBox="0 0 24 24" fill="none" stroke="#222" stroke-width="1.8"><circle cx="7" cy="7" r="4"/><circle cx="17" cy="7" r="4"/><circle cx="7" cy="17" r="4"/><circle cx="17" cy="17" r="4"/></svg>PORTFOLIO</div>
    <div class="navitem" style="left:981px;width:140px">
      <svg viewBox="0 0 24 24" fill="none" stroke="#222" stroke-width="1.8"><rect x="2" y="4" width="20" height="16" rx="1"/><path d="M5 16l4-5 3 3 4-6 3 3"/></svg>BACKTEST</div>
  </header>

  <div class="content"></div>

  <nav class="tabs">
    <div class="tab low" style="left:51px;width:143px">EQUITIES</div>
    <div class="tab low" style="left:198px;width:143px">ETFS</div>
    <div class="tab mid" style="left:346px;width:143px">PAIRS</div>
    <div class="tab current" style="left:494px;width:143px">ETF PAIRS</div>
    <div class="tab mid" style="left:641px;width:143px">FACTORS</div>
    <div class="tab low" style="left:789px;width:143px">NEW TAB TITLE #1</div>
    <div class="tab low" style="left:937px;width:143px">NEW TAB TITLE #2</div>
    <div class="tab arrow" style="left:1084px"><svg width="14" height="18" viewBox="0 0 14 18"><path d="M3 2l8 7-8 7" fill="none" stroke="#888" stroke-width="3"/></svg></div>
    <div class="tab add" style="left:1126px"><svg width="22" height="22" viewBox="0 0 22 22" fill="none" stroke="#fff" stroke-width="1.8"><circle cx="11" cy="11" r="9.5"/><path d="M11 6v10M6 11h10"/></svg></div>
  </nav>

  <div class="export" style="left:1061px">
    <svg width="24" height="22" viewBox="0 0 24 22" fill="none" stroke="#0b3a6e" stroke-width="2.2"><path d="M9 4H3v16h16v-6"/><path d="M8 15c1-6 5-9 12-9"/><path d="M16 2l5 4-4 5"/></svg>Export</div>

  <table class="grid" style="left:83px">
    <colgroup><col style="width:92px"><col style="width:129px"><col style="width:107px"><col style="width:78px"><col style="width:83px"><col style="width:83px"><col style="width:83px"><col style="width:83px"><col style="width:83px"><col style="width:83px"><col style="width:84px"><col style="width:83px"></colgroup>
    <thead><tr>
      <th class="key">ID <svg width="10" height="7" viewBox="0 0 10 7"><path d="M1 1l4 4 4-4" fill="none" stroke="#fff" stroke-width="2"/></svg></th>
      <th class="key">Sector</th><th class="key">Time</th>
      <th>Quality</th><th>Stat 1</th><th>Stat 2</th><th>Stat 3</th><th>Stat 4</th><th>Stat 5</th><th>Stat 6</th><th>Stat 7</th><th>Stat 8</th>
    </tr></thead>
    <tbody>
      <tr><td class="id">Model 1</td><td class="sector">Materials</td><td>2019-07-03<br>12:15:00.000</td><td>30.2288</td><td>2.01574</td><td>23.305</td><td>-0.149368</td><td>22.3054</td><td>4.63714</td><td>0.945706</td><td>2.81949</td><td>2.60858</td></tr>
      <tr><td class="id">Model 2</td><td class="sector">Industrials</td><td>2019-07-03<br>12:15:00.000</td><td>32.8694</td><td>0.87307</td><td>32.185</td><td>-0.033692</td><td>33.9911</td><td>11.5693</td><td>-0.472968</td><td>-0.830458</td><td>6.80646</td></tr>
      <tr><td class="id">Model 3</td><td class="sector">Consumer<br>Discretionary</td><td>2019-07-03<br>12:15:00.000</td><td>1.66002</td><td>-0.569222</td><td>159.814</td><td>0.0252328</td><td>172.616</td><td>10.2875</td><td>-0.750396</td><td>-0.385309</td><td>4.69146</td></tr>
      <tr><td class="id">Model 4</td><td class="sector">Information<br>Technology</td><td>2019-07-03<br>12:15:00.000</td><td>45.6856</td><td>0.412148</td><td>202.488</td><td>0.0084923</td><td>205.834</td><td>11.9094</td><td>-0.137913</td><td>0.449595</td><td>3.85106</td></tr>
      <tr><td class="id">Model 5</td><td class="sector">Information<br>Technology</td><td>2019-07-03<br>12:15:00.000</td><td>75.7733</td><td>7.06728</td><td>188.605</td><td>0.016913</td><td>161.665</td><td>3.82241</td><td>0.981019</td><td>1.29847</td><td>3.34927</td></tr>
    </tbody>
  </table>
</div>

<aside class="filters">
  <span>FILTERS</span>
  <svg width="26" height="26" viewBox="0 0 26 26"><circle cx="13" cy="13" r="12" fill="#fff"/><circle cx="13" cy="13" r="9" fill="#0b3a6e"/><path d="M8 13h9M13 9l4 4-4 4" fill="none" stroke="#fff" stroke-width="2"/></svg>
</aside>
</body>
</html>
```